Business Cards for IT Consulting Company (Managed Service Provider)

I am looking to have some business cards printed and would like some designs. We are an IT Consulting company based in Vancouver BC. I would like a nice clean and modern look to the cards. I have uploaded all the versions of my logo so parts can be used as needed. Here is a snippit from our website homepage:

Quillbrook Networks Ltd. is an IT Solutions Partner located in Vancouver BC, Canada. We offer IT solutions and support to customers in the greater Vancouver Area. With expertise in Microsoft platforms, as well as Linux and Mac OSX and over 12 years experience in the IT industry, Quillbrook Networks is dedicated to offering our clients top quality service and products. We take pride in the solutions we offer our customers. The greatest compliment a client can give us is to recommend our services.

Quillbrook Networks Ltd. offers a wide range of IT services from onsite service to remote support and managed service solutions. This allows clients to choose the support path that best suits their company’s needs. Supporting many different sized companies from small to enterprise level over the past 12 years Quillbrook Networks has the experience and expertise needed to ensure things run smoothly. Allowing our clients to focus on doing business.

Revolutionizing the way IT services are delivered.

Quillbrook Networks is dedicated to providing our clients with IT solutions that work and grow with them for years to come. This philosophy helps save money in the long run instead of replacing equipment constantly. Far too often IT solutions are not well thought out and while possibly solving the problem at hand, require replacement due to growth or quality within a very short time frame. Quillbrook Networks takes pride in providing solutions that will last and be able to accommodate growth without the need for replacement.

Industry/Entity Type

Information Technology

Contact Information for Business Card

Quillbrook Networks Ltd.
(Employee Name)
Eml: (Employees Email Address)
Web: quillbrook.me
Ph: 604-555-0148

Font styles to use
Serif
Sans Serif

Requirements
Must have
• The Company logo and company colors.
Nice to have
• - Our tag line: "Revolutionizing IT Services" or "Revolutionizing the way IT services are delivered."
• - Also I really like the idea of nature and technology together blending which is sort of where my logo came from so integrating that somehow onto the business cards would be great.

```html
<!DOCTYPE html>
<html lang="en">
<head>
<meta charset="utf-8">
<title>Quillbrook Networks Ltd. — Business Cards</title>
<link href="https://fonts.googleapis.com/css2?family=Montserrat:wght@500;600&family=Roboto:ital,wght@0,400;1,400&display=swap" rel="stylesheet">
<style>
  :root {
    --page-bg: #e4e4e4;
    --brand-blue: #1b90d6;
    --brand-blue-light: #2a9ee0;
    --card-white: #f4f4f4;
    --ink: #3a3a3a;
    --ink-soft: #555555;
    --rule: #dcdcdc;
    --band-grey: #555555;
  }
  * { margin: 0; padding: 0; box-sizing: border-box; }
  html, body {
    width: 1200px;
    height: 1200px;
    overflow: hidden;
    background: var(--page-bg);
  }
  .canvas {
    position: relative;
    width: 1200px;
    height: 1200px;
  }

  /* Front of card */
  .card-front {
    position: absolute;
    left: 238px;
    top: 118px;
    width: 712px;
    height: 419px;
    overflow: hidden;
  }
  .card-front__pattern {
    position: absolute;
    inset: 0;
    background: linear-gradient(180deg, var(--brand-blue-light) 0%, var(--brand-blue) 100%);
  }
  .card-front__wordmark {
    position: absolute;
    left: 0;
    right: 0;
    top: 180px;
    text-align: center;
    font-family: "Montserrat", sans-serif;
    font-weight: 600;
    font-size: 44px;
    letter-spacing: 0.5px;
    color: #ffffff;
  }

  /* Back of card */
  .card-back {
    position: absolute;
    left: 231px;
    top: 645px;
    width: 712px;
    height: 415px;
    background: var(--card-white);
    overflow: hidden;
  }
  .card-back__wordmark {
    position: absolute;
    left: 40px;
    top: 178px;
    width: 290px;
    text-align: center;
    font-family: "Montserrat", sans-serif;
    font-weight: 600;
    font-size: 26px;
    line-height: 1.3;
    color: var(--brand-blue);
  }
  .card-back__divider {
    position: absolute;
    left: 331px;
    top: 80px;
    width: 1px;
    height: 245px;
    background: var(--rule);
  }
  .contact {
    position: absolute;
    left: 389px;
    top: 122px;
  }
  .contact__name {
    font-family: "Montserrat", sans-serif;
    font-weight: 600;
    font-size: 26px;
    color: var(--brand-blue);
  }
  .contact__title {
    margin-top: 6px;
    font-family: "Roboto", sans-serif;
    font-style: italic;
    font-size: 17px;
    color: var(--ink-soft);
  }
  .contact__list {
    list-style: none;
    margin-top: 26px;
  }
  .contact__item {
    display: flex;
    align-items: center;
    height: 27.5px;
    font-family: "Roboto", sans-serif;
    font-size: 18px;
    color: var(--ink);
  }
  .contact__icon {
    width: 16px;
    height: 16px;
    margin-right: 19px;
    margin-left: 1px;
    flex: none;
  }
  .card-back__band {
    position: absolute;
    left: 0;
    bottom: 0;
    width: 340px;
    height: 25px;
    background: var(--band-grey);
  }
  .card-back__tagline-band {
    position: absolute;
    right: 0;
    bottom: 0;
    width: 400px;
    height: 52px;
  }
  .card-back__tagline {
    position: absolute;
    left: 389px;
    bottom: 15px;
    font-family: "Montserrat", sans-serif;
    font-weight: 500;
    font-size: 19px;
    color: #ffffff;
  }
</style>
</head>
<body>
<main class="canvas">

  <section class="card-front" aria-label="Business card front">
    <div class="card-front__pattern" role="img" aria-label="Blue background with faint repeating hexagon pattern"></div>
    <div class="card-front__wordmark">Quillbrook Networks Ltd.</div>
  </section>

  <section class="card-back" aria-label="Business card back">
    <div class="card-back__wordmark">Quillbrook Networks</div>
    <div class="card-back__divider"></div>

    <div class="contact">
      <div class="contact__name">Daniel Hart</div>
      <div class="contact__title">Managing Director</div>
      <ul class="contact__list">
        <li class="contact__item">
          <svg class="contact__icon" viewBox="0 0 16 16" aria-hidden="true">
            <path d="M2 5c0-2 2-3 6-3s6 1 6 3v1h-3V4.5H5V6H2z" fill="var(--brand-blue)"/>
            <path d="M4 7h8l2 6H2z" fill="var(--brand-blue)"/>
            <circle cx="8" cy="10" r="1.6" fill="#ffffff"/>
          </svg>
          604-555-0148
        </li>
        <li class="contact__item">
          <svg class="contact__icon" viewBox="0 0 16 16" aria-hidden="true">
            <circle cx="8" cy="8" r="6.5" fill="none" stroke="var(--brand-blue)" stroke-width="1.5"/>
            <ellipse cx="8" cy="8" rx="2.8" ry="6.5" fill="none" stroke="var(--brand-blue)" stroke-width="1.2"/>
            <line x1="1.5" y1="8" x2="14.5" y2="8" stroke="var(--brand-blue)" stroke-width="1.2"/>
          </svg>
          www.quillbrook.me
        </li>
        <li class="contact__item">
          <svg class="contact__icon" viewBox="0 0 16 16" aria-hidden="true">
            <rect x="1" y="3" width="14" height="10" fill="var(--brand-blue)"/>
            <polyline points="1,3.5 8,9 15,3.5" fill="none" stroke="#ffffff" stroke-width="1.3"/>
          </svg>
          support@quillbrook.me
        </li>
      </ul>
    </div>

    <div class="card-back__band"></div>
    <svg class="card-back__tagline-band" viewBox="0 0 400 52" preserveAspectRatio="none" aria-hidden="true">
      <polygon points="32,0 400,0 400,52 0,52" fill="var(--brand-blue)"/>
    </svg>
    <div class="card-back__tagline">Revolutionizing IT Services</div>
  </section>

</main>
</body>
</html>
```